Purple Heart Veteran Owned Telecommunications Company

I need to develop my current website (brightwirel.com) into something more upbeat and modern. I created the existing one with SiteKindle and it's very basic. I'm open to using any type of website builder and not just SiteKindle. I feel like SiteKindle is pretty basic. I want something customized to me and my company. I plan on doing a Zorbix Ad, Email Marketing, and Mail Marketing campaign and SEO push. I want a website built so they can look up my company. We are a low voltage telecommunications company based out of Chicago. We are a General Contractor and I have technicians all throughout the US and Canada. I mainly appeal to the government and fortune 500 companies across the country. I focus on commercial and federal work with minor work in Residential. I need to appeal to everyone and not just locally. My company name is Brightwirel. I'm a Marine Corps veteran and my I created the company with my son in mind. We are a service disabled veteran owned small business. I'm open to any play on my logo or color scheme. I do like the color blue but I'm open to anything again. I would like a website that has little maintenance needed and something that is modern and sticks out with my competitors. I'm only in business for 2 years but I need to stick out to my competition so I can start building revenue through ads and getting my name out there with limited funds. I did have a logo and name created which I'm attaching. I'm completely open to changing it if someone can come up with something creative. I would like someone that understands SEO and can help feed work to my site. I'm also open to paying more for the right website that gets everything I want. I know I need to add more pages and more professional. Please use my website as a template but also feel free to come up with any new ideas. I would like some feedback or ideas on what else to add to my website or remove so I can appeal to my audience and look more authentic.

Target Market(s)

Commercial Companies locally in Chicago, and Fortune 500 companies and the government

Industry/Entity Type

Telecommunications

Coding

Number of Pages Required

Font styles to use
Sans Serif

Requirements
Must have
• A Modern, fresh look that is customized and original. Something that sticks out to my customers.
Nice to have
• Anything that sticks out and isn't stock. I'm open to anything that is unique and different.
Should not have
• Nothing Generic. I would like something custom tailored to my business

```html
<!DOCTYPE html>
<html lang="en">
<head>
<meta charset="utf-8">
<title>Brightwirel – General Contractor</title>
<link rel="stylesheet" href="https://fonts.googleapis.com/css2?family=Rubik:wght@400;500;600;700&family=Lato:wght@400;700&display=swap">
<style>
:root{
  --navy:#14266b;
  --blue:#22409a;
  --blue-deep:#192f7a;
  --ink:#1b1b1f;
  --text:#3d3d45;
  --muted:#dfe2ec;
  --white:#ffffff;
  --black:#070707;
  --black-2:#0f0f10;
  --gold:#d99a3a;
}
*{box-sizing:border-box;margin:0;padding:0}
html,body{width:1200px;height:3982px;overflow:hidden}
body{position:relative;background:var(--white);font-family:'Lato',sans-serif;color:var(--text)}
.abs{position:absolute}
.head{font-family:'Rubik',sans-serif}
.btn{position:absolute;display:flex;align-items:center;justify-content:center;border-radius:30px;font-family:'Rubik',sans-serif;font-weight:600;font-size:13px;letter-spacing:.3px;text-transform:uppercase;color:var(--white);background:var(--navy)}
.btn.outline{background:transparent;border:2px solid var(--white)}
.rule{position:absolute;height:3px;width:62px;left:569px}

/* top bar & nav */
.topbar{top:0;left:0;width:1200px;height:36px;background:#f7f7f8;border-bottom:1px solid #e8e8ec}
.topbar span{position:absolute;top:9px;font-family:'Rubik',sans-serif;font-weight:500;font-size:14px;color:var(--ink);display:flex;align-items:center;gap:14px}
.nav{top:36px;left:0;width:1200px;height:84px;background:var(--white)}
.nav a{position:absolute;top:36px;font-family:'Rubik',sans-serif;font-weight:500;font-size:14px;color:var(--ink);text-decoration:none;text-transform:uppercase}
.nav a.active{color:var(--blue)}
.brand{top:82px;left:480px;width:240px;text-align:center;font-family:'Rubik',sans-serif;font-weight:600;font-size:26px;letter-spacing:2px;color:var(--navy)}

/* hero */
.hero-photo{top:120px;left:0;width:1200px;height:712px;background:linear-gradient(180deg,#7c8aa6 0%,#b6a58e 45%,#d79a48 72%,#8b5a2a 100%)}
.hero-title{top:266px;left:0;width:1200px;text-align:center;font-weight:700;font-size:47px;line-height:58px;color:var(--navy);letter-spacing:1px}
.dots{top:703px;left:568px;display:flex;gap:8px}
.dots i{width:17px;height:17px;border:2px solid var(--navy);border-radius:50%;display:block}
.dots i+i{width:14px;height:14px;margin-top:1px}

/* about */
.about-title{top:878px;left:0;width:1200px;text-align:center;font-weight:600;font-size:33px;color:var(--white)}
.about-copy{top:970px;left:245px;width:710px;text-align:center;font-size:16px;line-height:25px;color:#e6e9f5}
.card{position:absolute;width:291px;height:389px;background:var(--white);box-shadow:0 6px 18px rgba(0,0,0,.12);border-radius:4px;overflow:hidden;text-align:center}
.card .band{position:absolute;top:-20px;right:40px;width:28px;height:140px;background:var(--muted);transform:skewX(-30deg)}
.card .band.two{right:0;width:14px}
.card .icon{position:absolute;top:31px;left:82px;width:127px;height:127px;border-radius:50%;background:#d9dceb;display:flex;align-items:center;justify-content:center}
.card h3{position:absolute;top:184px;left:0;width:100%;font-family:'Rubik',sans-serif;font-weight:600;font-size:16px;color:var(--ink);letter-spacing:.4px}
.card p{position:absolute;top:218px;left:24px;width:243px;font-size:15px;line-height:23px;color:#333}

/* services */
.sec-title{left:0;width:1200px;text-align:center;font-weight:600;font-size:34px;color:var(--ink)}
.hex{position:absolute;top:1829px;width:293px;height:258px}
.hex-label{position:absolute;top:2110px;width:293px;text-align:center;font-family:'Rubik',sans-serif;font-weight:500;font-size:16px;letter-spacing:.6px;color:var(--ink)}
.hex-copy{position:absolute;top:1892px;left:498px;width:204px;text-align:center;font-size:14px;line-height:21px;color:#2b2b35}

/* news */
.news-card{position:absolute;top:2435px;width:433px;height:410px}
.news-photo{position:absolute;top:0;left:0;width:433px;height:278px}
.news-box{position:absolute;top:178px;left:24px;width:385px;height:232px;background:var(--white);border-radius:0 0 26px 0;padding:26px 32px}
.news-date{display:flex;align-items:center;gap:10px;font-family:'Rubik',sans-serif;font-weight:600;font-size:14px;color:var(--navy)}
.news-box h4{margin-top:14px;font-family:'Rubik',sans-serif;font-weight:500;font-size:14px;line-height:21px;color:var(--ink);text-transform:uppercase}
.news-box p{margin-top:7px;font-size:13px;line-height:20px;color:#555}

/* leader */
.lead-title{top:3053px;left:656px;width:440px;font-weight:600;font-size:31px;line-height:40px;color:var(--ink);letter-spacing:.8px}
.lead-copy{top:3176px;left:656px;width:430px;font-size:16px;line-height:25px;color:#3f3f48}

/* footer */
.footer{top:3502px;left:0;width:1200px;height:348px;background:var(--black)}
.subfoot{top:3850px;left:0;width:1200px;height:132px;background:var(--black-2)}
.foot-h{font-family:'Rubik',sans-serif;font-weight:500;font-size:22px;color:var(--white)}
.foot-line{position:absolute;left:144px;display:flex;gap:18px;font-family:'Rubik',sans-serif;font-size:15px;line-height:21px;color:var(--white)}
.foot-line svg{flex:none;margin-top:3px}
.news-input{top:3718px;left:798px;width:306px;height:48px;border:1.5px solid var(--white);border-radius:26px}
.news-input span{position:absolute;left:18px;top:14px;font-size:14px;color:#d0d0d0}
.news-input b{position:absolute;right:3px;top:3px;width:118px;height:39px;border-radius:22px;background:#3a3a3d;color:var(--white);font-family:'Rubik',sans-serif;font-weight:600;font-size:12px;display:flex;align-items:center;justify-content:center;letter-spacing:.4px}
.social{top:3897px;left:883px;display:flex;gap:11px}
.social i{display:block;width:35px;height:35px;border:1.5px solid var(--white);border-radius:50%}
</style>
</head>
<body>

<!-- top bar -->
<div class="abs topbar">
  <span style="left:143px">
    <svg width="15" height="15" viewBox="0 0 24 24"><path fill="#14266b" d="M6.6 10.8a15.1 15.1 0 0 0 6.6 6.6l2.2-2.2c.3-.3.7-.4 1-.2 1.1.4 2.3.6 3.6.6.6 0 1 .4 1 1V20c0 .6-.4 1-1 1A17 17 0 0 1 3 4c0-.6.4-1 1-1h3.5c.6 0 1 .4 1 1 0 1.3.2 2.5.6 3.6.1.3 0 .7-.2 1z"/></svg>
    847-555-0182
  </span>
  <span style="left:822px">
    <svg width="17" height="14" viewBox="0 0 24 18"><path fill="#14266b" d="M0 0h24v18H0z"/><path fill="#fff" d="M1.5 1.5 12 10l10.5-8.5v1.9L12 12 1.5 3.4z"/></svg>
    Support@brightwirel.com
  </span>
</div>

<nav class="abs nav">
  <a class="active" style="left:143px">Home</a>
  <a style="left:229px">Low Voltage</a>
  <a style="left:373px">About Us</a>
  <a style="left:732px">Markets</a>
  <a style="left:845px">Our Team</a>
  <a style="left:965px">Contact Us</a>
</nav>

<!-- hero -->
<div class="abs hero-photo" role="img" aria-label="Telecommunication towers in front of a city skyline at sunset"></div>
<svg class="abs" style="top:118px;left:0" width="1200" height="50" viewBox="0 0 1200 50" aria-hidden="true">
  <path d="M0 0H1200V2H720L690 46H510L480 2H0Z" fill="#ffffff"/>
</svg>
<div class="abs brand">BRIGHTWIREL</div>
<div class="abs head hero-title">BRIGHTWIREL<br>WITH OVER 20 YEARS<br>OF PROVEN EXPERIENCE</div>
<div class="btn" style="top:460px;left:506px;width:188px;height:46px;font-size:14px">Learn More</div>
<div class="abs dots"><i></i><i></i><i></i></div>

<!-- about -->
<svg class="abs" style="top:780px;left:0" width="1200" height="745" viewBox="0 0 1200 745" role="img" aria-label="Team working together, tinted blue">
  <defs>
    <linearGradient id="aboutFill" x1="0" y1="0" x2="1" y2="1">
      <stop offset="0" stop-color="#1d3584"/>
      <stop offset=".5" stop-color="#2a4a9e"/>
      <stop offset="1" stop-color="#1a2f7c"/>
    </linearGradient>
  </defs>
  <path d="M0 52L600 0L1200 52V645L600 740L0 645Z" fill="url(#aboutFill)"/>
</svg>
<div class="abs head about-title">ABOUT BRIGHTWIREL</div>
<div class="rule" style="top:938px;background:var(--white)"></div>
<p class="abs about-copy">Sed ut perspiciatis unde omnis iste natus error sit voluptatem accusantium doloremque laudantium, totam rem aperiam, eaque ipsa quae ab illo inventore veritatis et quasi architecto beatae vitae dicta sunt explicabo. Nemo enim ipsam voluptatem quia voluptas sit aspernatur aut odit aut fugit, sed quia consequuntur magni dolores eos qui ratione voluptatem</p>
<div class="btn outline" style="top:1095px;left:520px;width:160px;height:50px">Learn More</div>

<div class="card" style="top:1203px;left:144px">
  <div class="band"></div><div class="band two"></div>
  <div class="icon">
    <svg width="66" height="60" viewBox="0 0 66 60" fill="none" stroke="#14266b" stroke-width="2.4"><rect x="3" y="3" width="60" height="44" rx="3"/><path d="M3 13h60"/><circle cx="10" cy="8" r="1.5"/><circle cx="16" cy="8" r="1.5"/><circle cx="22" cy="8" r="1.5"/><path d="M20 40l14-14M26 22l6 6M40 26l8 14M22 55h22M33 47v8"/></svg>
  </div>
  <h3>WHAT WE DO</h3>
  <p>Our past projects include both new construction and repairs/restorations. Occupied and fully operational job sites are never a problem. And we can also plan, manage, and design jobs.</p>
</div>

<div class="card" style="top:1235px;left:456px;height:388px">
  <div class="band"></div><div class="band two"></div>
  <div class="icon">
    <svg width="62" height="62" viewBox="0 0 62 62" fill="none" stroke="#14266b" stroke-width="2.4"><circle cx="31" cy="31" r="27"/><path d="M8 38l14-8 9 6 9-6 14 8M22 30l9 12 9-12"/><circle cx="31" cy="20" r="6"/></svg>
  </div>
  <h3>WORKING TOGETHER</h3>
  <p>We offer an end-to-end client experience that includes seamless communication, budgeting, staffing, on-site organization, and solid, quality handiwork every time.</p>
</div>

<div class="card" style="top:1203px;left:767px">
  <div class="band"></div><div class="band two"></div>
  <div class="icon">
    <svg width="56" height="62" viewBox="0 0 56 62" fill="none" stroke="#14266b" stroke-width="2.4"><rect x="4" y="4" width="38" height="54" rx="2"/><path d="M12 16h22M12 24h22M12 32h22M12 40h14M46 10l6 4-16 28-6 2 0-6z"/></svg>
  </div>
  <h3>TRUST</h3>
  <p style="left:52px;width:187px">We are committed to building trust among our clients, contractors, colleagues, and community</p>
</div>

<!-- services -->
<div class="abs head sec-title" style="top:1715px">OUR SERVICES</div>
<div class="rule" style="top:1772px;background:var(--ink)"></div>

<svg class="hex" style="left:144px" viewBox="0 0 293 258" role="img" aria-label="Glowing copper cable strands">
  <defs><radialGradient id="hexCable" cx=".55" cy=".55" r=".6"><stop offset="0" stop-color="#ffd37a"/><stop offset=".45" stop-color="#e2582b"/><stop offset="1" stop-color="#4a1610"/></radialGradient></defs>
  <path d="M73 0H220L293 129L220 258H73L0 129Z" fill="url(#hexCable)"/>
</svg>
<svg class="hex" style="left:454px" viewBox="0 0 293 258" role="img" aria-label="Digital network panel in light blue">
  <defs><linearGradient id="hexNet" x1="0" y1="0" x2="0" y2="1"><stop offset="0" stop-color="#f2f5fb"/><stop offset="1" stop-color="#b9cde8"/></linearGradient></defs>
  <path d="M75 3H218L290 129L218 255H75L3 129Z" fill="url(#hexNet)" stroke="#1e3a96" stroke-width="5"/>
</svg>
<p class="hex-copy">Sed ut perspiciatis unde omnis iste natus voluptatem accusantium doloremque laudantium, totam rem aperiam, eaque</p>
<div class="btn" style="top:2012px;left:531px;width:138px;height:32px;font-size:12px">Learn More</div>
<svg class="hex" style="left:763px" viewBox="0 0 293 258" role="img" aria-label="Technician with a laptop in a server room">
  <defs><linearGradient id="hexInstall" x1="0" y1="0" x2="1" y2="1"><stop offset="0" stop-color="#2b3b63"/><stop offset=".55" stop-color="#8aa6cf"/><stop offset="1" stop-color="#cfd9ea"/></linearGradient></defs>
  <path d="M73 0H220L293 129L220 258H73L0 129Z" fill="url(#hexInstall)"/>
</svg>
<div class="hex-label" style="left:144px">CABILING</div>
<div class="hex-label" style="left:454px">NETWORK</div>
<div class="hex-label" style="left:763px">INSTALLATION</div>

<!-- latest news -->
<svg class="abs" style="top:2216px;left:0" width="1200" height="730" viewBox="0 0 1200 730" role="img" aria-label="Office team in a meeting, tinted navy">
  <defs><linearGradient id="newsFill" x1="0" y1="0" x2="1" y2="1"><stop offset="0" stop-color="#182b72"/><stop offset=".5" stop-color="#223f92"/><stop offset="1" stop-color="#172a70"/></linearGradient></defs>
  <path d="M0 74L600 0L1200 74Z" fill="#3a3a40"/>
  <path d="M0 80L600 8L1200 80V729H0Z" fill="url(#newsFill)"/>
</svg>
<div class="abs head sec-title" style="top:2316px;color:var(--white)">LATEST NEWS</div>
<div class="rule" style="top:2373px;background:var(--white)"></div>

<article class="news-card" style="left:144px">
  <div class="news-photo" role="img" aria-label="Blue network cables plugged into a patch panel" style="background:linear-gradient(135deg,#3d9fb0,#e9d6a2 55%,#6b4a7d)"></div>
  <div class="news-box">
    <div class="news-date"><svg width="18" height="18" viewBox="0 0 18 18"><circle cx="9" cy="9" r="9" fill="#14266b"/><rect x="5" y="5.5" width="8" height="7" fill="none" stroke="#fff" stroke-width="1.2"/><path d="M5 8h8" stroke="#fff"/></svg>Jun 15,2021</div>
    <h4>Nemo enim ipsam voluptatem<br>quia voluptas sit</h4>
    <p>Sed ut perspiciatis unde omnis iste natus error sit voluptatem accusantium doloremque laudantium, totam rem aperiam, eaque ipsa quae ab illo</p>
  </div>
  <div class="btn" style="top:2792px;margin-top:-2435px;left:55px;width:140px;height:33px;font-size:12px">Learn More</div>
</article>

<article class="news-card" style="left:625px">
  <div class="news-photo" role="img" aria-label="Man on a phone call at his desk" style="background:linear-gradient(135deg,#2b3347,#5e6b82 50%,#b08c6e)"></div>
  <div class="news-box">
    <div class="news-date"><svg width="18" height="18" viewBox="0 0 18 18"><circle cx="9" cy="9" r="9" fill="#14266b"/><rect x="5" y="5.5" width="8" height="7" fill="none" stroke="#fff" stroke-width="1.2"/><path d="M5 8h8" stroke="#fff"/></svg>Jun 15,2021</div>
    <h4>Nemo enim ipsam voluptatem<br>quia voluptas sit</h4>
    <p>Sed ut perspiciatis unde omnis iste natus error sit voluptatem accusantium doloremque laudantium, totam rem aperiam, eaque ipsa quae ab illo</p>
  </div>
  <div class="btn" style="top:2792px;margin-top:-2435px;left:55px;width:140px;height:33px;font-size:12px">Learn More</div>
</article>

<!-- leader -->
<svg class="abs" style="top:3012px;left:144px" width="470" height="405" viewBox="0 0 470 405" role="img" aria-label="Data centre servers with cloud network icons">
  <defs><linearGradient id="leadFill" x1="0" y1="0" x2="1" y2="1"><stop offset="0" stop-color="#2f7f9a"/><stop offset=".5" stop-color="#1b2b44"/><stop offset="1" stop-color="#0d1422"/></linearGradient></defs>
  <path d="M0 405L120 200L240 405Z" fill="#f1f2f6"/>
  <path d="M0 0H470L232 405Z" fill="url(#leadFill)"/>
</svg>
<h2 class="abs head lead-title">LEADER IN STRUCTURED CABLING, WIRING, AND NETWORKING SERVICE</h2>
<p class="abs lead-copy">Sed ut perspiciatis unde omnis iste natus error sit voluptatem accusantium doloremque laudantium, totam rem aperiam, eaque ipsa quae ab illo inventore veritatis et quasi architecto beatae vitae dicta sunt explicabo. Nemo enim ipsam voluptatem quia voluptas sit aspernatur aut odit aut fugit</p>
<div class="btn" style="top:3349px;left:656px;width:156px;height:44px">Learn More</div>

<!-- footer -->
<footer>
  <div class="abs footer"></div>
  <div class="abs subfoot"></div>
  <div class="abs foot-h" style="top:3594px;left:144px">Contact Us</div>
  <div class="foot-line" style="top:3658px">
    <svg width="12" height="16" viewBox="0 0 12 16"><path fill="#fff" d="M6 0a6 6 0 0 0-6 6c0 4.5 6 10 6 10s6-5.5 6-10a6 6 0 0 0-6-6zm0 8.5A2.5 2.5 0 1 1 6 3.5a2.5 2.5 0 0 1 0 5z"/></svg>
    <span>Brightwirel<br>201 ipsam voluptatem quia<br>voluptas sit aspernatur</span>
  </div>
  <div class="foot-line" style="top:3732px">
    <svg width="14" height="14" viewBox="0 0 24 24"><path fill="#fff" d="M6.6 10.8a15.1 15.1 0 0 0 6.6 6.6l2.2-2.2c.3-.3.7-.4 1-.2 1.1.4 2.3.6 3.6.6.6 0 1 .4 1 1V20c0 .6-.4 1-1 1A17 17 0 0 1 3 4c0-.6.4-1 1-1h3.5c.6 0 1 .4 1 1 0 1.3.2 2.5.6 3.6.1.3 0 .7-.2 1z"/></svg>
    <span>Phone: 847-555-0182</span>
  </div>
  <div class="foot-line" style="top:3780px">
    <svg width="16" height="13" viewBox="0 0 24 18"><path fill="#fff" d="M0 0h24v18H0z"/><path fill="#070707" d="M1.5 1.5 12 10l10.5-8.5v1.9L12 12 1.5 3.4z"/></svg>
    <span>Email: Support@brightwirel.com</span>
  </div>

  <div class="abs foot-h" style="top:3590px;left:798px">Sign up for newsletter</div>
  <p class="abs" style="top:3658px;left:798px;width:300px;font-size:13px;line-height:23px;color:#d8d8d8">Excepteur sint occaecat cupidatat non proident, sunt in culpa qui Nemo enim ipsam vo-</p>
  <div class="abs news-input"><span>Enter Email</span><b>SUBSCRIBE</b></div>

  <p class="abs" style="top:3905px;left:144px;font-family:'Rubik',sans-serif;font-size:15px;color:var(--white)">Brightwirel © 2021 All Rights Reserved</p>
  <div class="abs social" aria-label="Social links"><i></i><i></i><i></i><i></i></div>
</footer>

</body>
</html>
```